wardrobe/costume stylist needs good business card for own business

Hi:)

I'm wanting a business card for my company. I am a freelance stylist.

I do wardrobe/costume stylist to TV commercials; Films; Fashion and Lifestyle shoots.

I'd like a design based around my name Rosalind Parfrey written nicely, maybe a colour? Up to you?!

I've attached a couple of images of business cards I like
.... be creative and have fun!

Thank you :)

Reason: I was trying to get my new business card ready for before I headed overseas Friday morning but I don't think that was realistic so I'd like to extend the deadline to give time to the project. Thank you

Hi designers:) Thank you for all your designs, I've extended the deadline until Sunday, so there's a bit more time. I've attached 3 pictures of business cards which I quite like, please take a look to see if it can be of help in your process. I like the pale plain or patterned background with dark font and the dark plain or patterned background with the pale font the motifs the feminine fonts the plain fonts I like the idea of playing with a circle or some shape on one side of the card with my name or initials as in the picture I have on my post could you play around with this idea a bit please? Thank you all for the work you've done :) Rosa

Hi I am working overseas til Saturday night sorry for no feedback until I teturn Thanks :) Rosa

Hi designers, Thank you all so much for submitting your designs, I really appreciate your input into my project :) I'm sorry I didn't get to respond to some comments, and give feedback. I didn't back from being away until later than I expected, and the deadline had passed then, so apologies. Thanks to you all again for all your really good designs :) Rosa

Target Market(s)

I am a freelance stylist my target audience is producers, production companies, photographers, directors...

Industry/Entity Type

Business

Requirements
Must have
• Rosalind Parfrey
Stylist or Wardrobe Stylist

email rosaparfrey@mailbox-example.co.nz
Mobile 0218467193

(Don't have to use the words 'email' and 'mobile')
Nice to have
• Would like it to be double sided
Like B & W
Like pale colour background with dark font or white font
Like dark colour background with pale font
Should not have
• I would prefer it not to incorporate pictures

```html
<!DOCTYPE html>
<html lang="en">
<head>
<meta charset="utf-8">
<title>Rosalind Parfrey – Wardrobe Stylist Business Card</title>
<link rel="stylesheet" href="https://fonts.googleapis.com/css2?family=Playball&family=Arimo:wght@400;700&display=swap">
<style>
  :root {
    --backdrop: #e9e9ea;
    --magenta: #ec0c8c;
    --ink: #0d0d0f;
    --white: #ffffff;
    --rail-blue: #5f86a8;
    --rail-pale: #c9d4dc;
    --rail-denim: #35506e;
    --rail-warm: #c98a72;
  }
  * { box-sizing: border-box; margin: 0; padding: 0; }
  html, body {
    width: 1200px; height: 480px; overflow: hidden;
    background: var(--backdrop);
  }
  .sheet {
    position: relative; width: 1200px; height: 480px;
    display: flex; gap: 30px; align-items: center; justify-content: center;
  }
  .card {
    position: relative; width: 560px; height: 311px; overflow: hidden;
    box-shadow: 0 6px 18px rgba(0,0,0,0.18);
  }
  .card-front { background: var(--magenta); }
  .card-shape { position: absolute; inset: 0; width: 100%; height: 100%; }

  .monogram {
    position: absolute; display: flex; align-items: center; justify-content: center;
    width: 66px; height: 66px; border-radius: 50%;
    border: 3px solid var(--white); background: var(--ink);
    color: var(--white);
    font-family: "Arimo", Arial, sans-serif; font-weight: 700; font-size: 22px;
    letter-spacing: 1px;
  }
  .card-front .monogram { left: 103px; top: 78px; }

  .name-script {
    position: absolute; color: var(--white);
    font-family: "Playball", cursive; font-weight: 400; white-space: nowrap;
  }
  .name-left { left: 22px; top: 162px; width: 228px; text-align: center; font-size: 36px; }
  .name-right { left: 292px; top: 58px; font-size: 38px; }

  .role {
    position: absolute; left: 296px; top: 110px; color: var(--white);
    font-family: "Arimo", Arial, sans-serif; font-size: 13px; font-weight: 400;
    letter-spacing: 0.3px; text-transform: uppercase;
  }
  .contact-list { position: absolute; left: 296px; top: 144px; list-style: none; }
  .contact-item {
    display: flex; align-items: center; gap: 10px; height: 30px;
    color: var(--white); font-family: "Arimo", Arial, sans-serif; font-size: 13px;
  }
  .contact-icon { width: 18px; height: 18px; flex: none; }

  .card-back { background: var(--magenta); }
  .rail-photo {
    position: absolute; left: 0; top: 0; width: 560px; height: 278px;
    background: linear-gradient(100deg, var(--rail-pale) 0%, var(--rail-blue) 18%,
      var(--rail-warm) 34%, var(--rail-denim) 50%, var(--rail-blue) 68%, var(--rail-pale) 100%);
  }
  .card-back .monogram { left: 445px; top: 140px; width: 74px; height: 74px; font-size: 24px; }
</style>
</head>
<body>
<main class="sheet">

  <section class="card card-front" aria-label="Card front">
    <svg class="card-shape" viewBox="0 0 560 311" aria-hidden="true">
      <path fill="var(--ink)" d="M0 12 H250 Q262 12 262 24 V34 Q262 44 272 44 V267 Q262 267 262 277 V287 Q262 299 250 299 H0 Z"/>
    </svg>
    <div class="monogram">RP</div>
    <div class="name-script name-left">Rosalind Parfrey</div>

    <div class="name-script name-right">Rosalind Parfrey</div>
    <div class="role">Wardrobe Stylist</div>
    <ul class="contact-list">
      <li class="contact-item">
        <svg class="contact-icon" viewBox="0 0 18 18" aria-hidden="true">
          <rect x="1" y="4" width="16" height="11" fill="var(--white)"/>
          <path d="M1 4 L9 10 L17 4" fill="none" stroke="var(--magenta)" stroke-width="1.4"/>
        </svg>
        rosaparfrey@mailbox-example.co.nz
      </li>
      <li class="contact-item">
        <svg class="contact-icon" viewBox="0 0 18 18" aria-hidden="true">
          <rect x="4.5" y="1" width="9" height="16" rx="2" fill="none" stroke="var(--white)" stroke-width="1.6"/>
          <rect x="8" y="13.5" width="2" height="1.5" fill="var(--white)"/>
        </svg>
        0218467193
      </li>
    </ul>
  </section>

  <section class="card card-back" aria-label="Card back">
    <div class="rail-photo" role="img" aria-label="Photograph of clothes hanging on a wardrobe rail"></div>
    <svg class="card-shape" viewBox="0 0 560 311" aria-hidden="true">
      <path fill="var(--magenta)" d="M0 278 H200 Q210 278 210 270 Q210 262 220 262 H340 Q350 262 350 270 Q350 278 360 278 H560 V311 H0 Z"/>
    </svg>
    <div class="monogram">RP</div>
  </section>

</main>
</body>
</html>
```